Redesign Comparisson chart - make modern and effective

Use your imaginations to make a powerful distinction between KMV & other holistic modalities. There are 7 elements physical, mental, emotional, energetic, subconscious, superconscious and before and after testing.
We want it to be obvious that KMV is the only modality that works on all these elements simultaneously. We do not want to include any chakras as we want this information to be accepted by a wide range of people and belief systems.'

We want it to look simple but effective. Professional but powerful. We want KMV to stand out even of you eye just passed over i.
Updates

Hi everyone, thanks for your submissions so far. Basically what this image is meant to represent is a comparison chart between all the modalities There are 5 elements physical, mental, emotional, subconscious and superconscious. we want to reflect that KMV is the only modality that works on all these elements simultaneously. As we want the concept to be accepted and not considered woo woo, we want to steer away from chakras.

Target Market(s)

Professionals

Industry/Entity Type

Professional services

Font styles to use
Sans Serif
Other font styles liked:
• Poppins Monserratt

Colors
0094D4
00A9DD
6FCCEA
C7EBF8
E9F6FB

Requirements
Must have
• Clear/professional and clean look. Brand colours and logos. All typography and formats must be cohesive.
Nice to have
• More easy to read, different layout
Should not have
• Do not change the data just the way its presented. No chakras

```html
<!DOCTYPE html>
<html lang="en">
<head>
<meta charset="utf-8">
<title>KMV Modality Comparison Chart</title>
<link href="https://fonts.googleapis.com/css2?family=Montserrat:wght@400;500;600;700;800&family=Poppins:wght@600;700&display=swap" rel="stylesheet">
<style>
:root{
  --brand:#0094d4;
  --brand-2:#00a9dd;
  --brand-3:#6fccea;
  --brand-4:#c7ebf8;
  --brand-5:#e9f6fb;
  --panel:#1186d0;
  --panel-glow:#7fd0f2;
  --line:rgba(255,255,255,.28);
  --physical:#f23c14;
  --mental:#1a8fd6;
  --emotional:#8dc63f;
  --energetic:#f7a13b;
  --sub:#f5e82a;
  --super:#6a2c91;
  --before:#c2188b;
  --white:#ffffff;
}
*{box-sizing:border-box;margin:0;padding:0}
html,body{width:872px;height:1200px;overflow:hidden;background:var(--white)}
body{font-family:"Montserrat",Arial,sans-serif}
.sheet{position:relative;width:800px;height:1100px;transform:scale(1.09);transform-origin:0 0}
.band{position:absolute;left:0;top:100px;width:800px;height:715px;background:var(--brand-4)}
.headline{position:absolute;left:303px;top:34px;width:460px;font-family:"Poppins",sans-serif;font-weight:700;font-size:15.5px;color:var(--brand)}
.intro{position:absolute;left:294px;top:53px;width:470px;font-size:7.6px;line-height:10.5px;font-weight:600;color:#1c6ea8;letter-spacing:-.1px}
.panel{position:absolute;left:82px;top:82px;width:688px;height:748px;border-radius:6px;
  background:radial-gradient(ellipse 320px 360px at 370px 330px,var(--panel-glow) 0%,#2aa6e6 45%,var(--panel) 100%);
  box-shadow:0 4px 10px rgba(0,60,110,.25)}
.brand-box{position:absolute;left:100px;top:65px;width:158px;height:66px;background:var(--white);border:4px solid var(--brand-2);border-radius:3px;display:flex;align-items:center;gap:8px;padding-left:12px}
.brand-box .square{width:14px;height:14px;background:var(--brand-2)}
.brand-box .name{font-weight:700;font-size:13px;color:var(--brand-2);white-space:nowrap}
.tab{position:absolute;bottom:967px;width:65px;border:2px solid var(--white);border-bottom:none;border-radius:4px 4px 0 0;display:flex;align-items:center;justify-content:center;text-align:center;font-size:7.2px;font-weight:700;color:var(--white);line-height:8px;text-transform:uppercase}
.grid{position:absolute;left:82px;top:133px;width:671px}
.row{display:grid;grid-template-columns:199px repeat(7,67.43px);border-top:1px solid var(--line)}
.row>div{border-left:1px solid var(--line);display:flex;align-items:center;justify-content:center}
.row>.label{border-left:none;justify-content:flex-start;padding-left:18px;font-size:11px;font-weight:500;line-height:16px;color:var(--white);background:rgba(255,255,255,.05)}
.row:last-child{border-bottom:1px solid var(--line)}
.mark{width:11px;height:11px;border-radius:50%;border:1.5px solid var(--white)}
.mark.hollow{background:var(--mental)}
.row.feature{border-top:none;position:relative}
.highlight{position:absolute;left:47px;top:437px;width:733px;height:38px;border:1.5px solid rgba(255,255,255,.8);border-radius:4px;background:rgba(255,255,255,.45);box-shadow:0 2px 8px rgba(0,60,110,.3)}
.feature-name{position:absolute;left:100px;top:440px;height:32px;display:flex;align-items:center;font-size:9.5px;font-weight:800;color:var(--brand);text-transform:uppercase;white-space:nowrap}
.feature .mark{width:19px;height:19px}
.note{position:absolute;padding:5px 10px 6px 12px;font-size:9.4px;line-height:12px;color:var(--white);text-align:justify}
.note b{font-family:Georgia,serif;font-weight:700;font-size:11.5px;text-transform:uppercase}
.note.left{left:88px;width:332px}
.note.right{left:432px;width:338px}
</style>
</head>
<body>
<div class="sheet">
  <div class="band"></div>
  <h1 class="headline">Choose KMV For Fast, Immediate and Powerful Results.</h1>
  <p class="intro">I must experience healing on all levels I am not just a body I want to learn how to heal myself so I'm not dependent on others. I want to release all my emotional and mental blocks so I can be the best version of myself.</p>

  <div class="panel"></div>

  <div class="tab" style="left:281px;height:23px;background:var(--physical)">Physical</div>
  <div class="tab" style="left:349px;height:23px;background:var(--white);color:var(--mental)">Mental</div>
  <div class="tab" style="left:416px;height:29px;background:var(--emotional)">Emotional</div>
  <div class="tab" style="left:483px;height:29px;background:var(--energetic)">Energetic</div>
  <div class="tab" style="left:551px;height:41px;background:var(--sub);color:var(--mental)">Sub<br>Conscious</div>
  <div class="tab" style="left:618px;height:41px;background:var(--super)">Super<br>Conscious</div>
  <div class="tab" style="left:686px;height:48px;background:var(--before)">Before<br>&amp; After<br>Testing</div>

  <div class="brand-box"><span class="square"></span><span class="name">Kind Mind Vitality</span></div>

  <div class="highlight"></div>

  <div class="grid">
    <div class="row" style="height:99px"><div class="label">MASSAGE<br>YOGA<br>NATROPATHY<br>AYURVEDIC MEDICINE<br>WESTERN MEDICINE</div><div><span class="mark" style="background:var(--physical)"></span></div><div></div><div></div><div></div><div></div><div></div><div></div></div>
    <div class="row" style="height:32px"><div class="label">PSYCHIC INTUITIVE</div><div><span class="mark" style="background:var(--physical)"></span></div><div><span class="mark hollow"></span></div><div></div><div></div><div></div><div></div><div></div></div>
    <div class="row" style="height:32px"><div class="label">FAMILY CONSTELLATION</div><div><span class="mark" style="background:var(--physical)"></span></div><div><span class="mark hollow"></span></div><div></div><div><span class="mark" style="background:var(--energetic)"></span></div><div></div><div></div><div></div></div>
    <div class="row" style="height:32px"><div class="label">ACUPUNCTURE</div><div><span class="mark" style="background:var(--physical)"></span></div><div></div><div></div><div><span class="mark" style="background:var(--energetic)"></span></div><div></div><div></div><div></div></div>
    <div class="row" style="height:32px"><div class="label">NUTRITIONAL HEALING</div><div><span class="mark" style="background:var(--physical)"></span></div><div></div><div></div><div></div><div></div><div></div><div><span class="mark" style="background:var(--before)"></span></div></div>
    <div class="row" style="height:32px"><div class="label">CHINESE MEDICINE</div><div><span class="mark" style="background:var(--physical)"></span></div><div></div><div></div><div><span class="mark" style="background:var(--energetic)"></span></div><div></div><div></div><div><span class="mark" style="background:var(--before)"></span></div></div>
    <div class="row" style="height:47px"><div class="label">KINESIOLOGY<br>BOWEN THERAPY</div><div><span class="mark" style="background:var(--physical)"></span></div><div></div><div></div><div></div><div><span class="mark" style="background:var(--sub)"></span></div><div></div><div><span class="mark" style="background:var(--before)"></span></div></div>
    <div class="row feature" style="height:35px"><div class="label" style="background:none"></div><div><span class="mark" style="background:var(--physical)"></span></div><div><span class="mark" style="background:var(--mental)"></span></div><div><span class="mark" style="background:var(--emotional)"></span></div><div><span class="mark" style="background:var(--energetic)"></span></div><div><span class="mark" style="background:var(--sub)"></span></div><div><span class="mark" style="background:var(--super)"></span></div><div><span class="mark" style="background:var(--before)"></span></div></div>
    <div class="row" style="height:32px"><div class="label">EFT</div><div><span class="mark" style="background:var(--physical)"></span></div><div><span class="mark" style="background:var(--mental)"></span></div><div></div><div></div><div><span class="mark" style="background:var(--sub)"></span></div><div></div><div><span class="mark" style="background:var(--before)"></span></div></div>
    <div class="row" style="height:32px"><div class="label">CHIROPRATIC</div><div><span class="mark" style="background:var(--physical)"></span></div><div></div><div></div><div><span class="mark" style="background:var(--energetic)"></span></div><div><span class="mark" style="background:var(--sub)"></span></div><div></div><div><span class="mark" style="background:var(--before)"></span></div></div>
    <div class="row" style="height:47px"><div class="label">REIKI<br>CRYSTAL HEALING</div><div></div><div></div><div></div><div><span class="mark" style="background:var(--energetic)"></span></div><div></div><div></div><div></div></div>
    <div class="row" style="height:32px"><div class="label">ENERGY MEDICINE</div><div></div><div></div><div></div><div><span class="mark" style="background:var(--energetic)"></span></div><div></div><div></div><div><span class="mark" style="background:var(--before)"></span></div></div>
    <div class="row" style="height:32px"><div class="label">THETA HEALING</div><div></div><div></div><div></div><div></div><div><span class="mark" style="background:var(--sub)"></span></div><div><span class="mark" style="background:var(--super)"></span></div><div></div></div>
    <div class="row" style="height:32px"><div class="label">PSHYCHOLOGY</div><div></div><div><span class="mark hollow"></span></div><div></div><div></div><div></div><div></div><div></div></div>
    <div class="row" style="height:47px"><div class="label">MINDFULLNESS MEDITATION<br>LIFE COACHING</div><div></div><div><span class="mark hollow"></span></div><div></div><div></div><div></div><div></div><div><span class="mark" style="background:var(--before)"></span></div></div>
    <div class="row" style="height:48px"><div class="label">HYPNOTHERAPY<br>INNER CHILD HEALING</div><div></div><div><span class="mark hollow"></span></div><div></div><div></div><div><span class="mark" style="background:var(--sub)"></span></div><div></div><div></div></div>
    <div class="row" style="height:48px"><div class="label">NLP<br>TIMELINE THERAPY</div><div></div><div><span class="mark hollow"></span></div><div></div><div></div><div><span class="mark" style="background:var(--sub)"></span></div><div></div><div><span class="mark" style="background:var(--before)"></span></div></div>
  </div>

  <div class="feature-name">Kind Mind Vitality</div>

  <p class="note left" style="top:852px;height:78px;background:var(--physical)"><b>Physical</b> Most modalities, including a western medicine, focus on and treat the physical body only. The KMV process enables you to engage in healing your own body during the session. There is no muscle testing, no hands-on healing and no herbal remedies or medicines.</p>
  <p class="note left" style="top:937px;height:49px;background:var(--mental)"><b>Mental</b> KMV enables you to use your own consciousness to self-heal. We don't give you advice or coaching, we allow your mind to heal itself.</p>
  <p class="note left" style="top:994px;height:74px;background:var(--emotional)"><b>Emotional</b> KMV is the only modality that engages your emotions on a physical level. Emotions get stuck in your body and can cause illness over time if left unchecked. KMV enables you to experience fast and powerful emotional releasing.</p>

  <p class="note right" style="top:852px;height:47px;background:var(--energetic)"><b>Energetic</b> Most modalities try to move the energy in your body for you. KMV enables and empowers you to do it yourself.</p>
  <p class="note right" style="top:915px;height:51px;background:var(--sub)"><b>Subconscious</b> Some modalities, like Kinesiology, access your subconscious through muscle testing. KMV empowers you to access your own subconscious and heal it yourself.</p>
  <p class="note right" style="top:977px;height:37px;background:var(--super)"><b>Superconscious</b> KMV is the only modality that enables you to access and heal your superconscious mind yourself.</p>
  <p class="note right" style="top:1022px;height:52px;background:var(--before)"><b>Before &amp; After Testing</b> KMV is the only modality that enables you to provide before and after results, which are documented by us, and analysed by you with our help.</p>
</div>
</body>
</html>
```